Website Design for Wheels for Servicemen.org - Donated Cars to Disabled Vets

Need a Wordpress website. The coding now, esp. the CDONT coding is not supported by many hosting sites. Looking for a landing page to generate leads.

Logo Text

look at current one for ideas

Coding

Coded - Design and coding required

Number of Pages Required

1 page

Requirements
Must have
• look at current website at www.wheelsforservicemen.org
Nice to have
• look at this site: http://givevehicletoservicemen.org

```html
<!DOCTYPE html>
<html lang="en">
<head>
<meta charset="utf-8">
<title>Wheels for Servicemen – Donate Your Car</title>
<link href="https://fonts.googleapis.com/css2?family=Montserrat:wght@400;500;600&family=Open+Sans:wght@400;600&display=swap" rel="stylesheet">
<style>
:root{
  --blue:#0b6dd1;
  --red:#a81c1c;
  --nav:#454545;
  --ink:#333;
  --muted:#888;
  --line:#d6d6d6;
  --gray-band:#f4f4f4;
  --footer:#f1f1f1;
  --white:#fff;
}
*{box-sizing:border-box;margin:0;padding:0}
html,body{width:782px;height:1200px;overflow:hidden;background:var(--white)}
body{position:relative;font-family:'Open Sans',Arial,sans-serif;color:var(--ink)}
.abs{position:absolute}

/* header */
.brand{left:86px;top:20px;display:flex;align-items:center;gap:8px}
.brand-mark{width:22px;height:22px;background:var(--red);border-radius:3px}
.brand-name{font-family:'Montserrat',sans-serif;font-size:21px;font-weight:500;color:var(--blue)}
.helpline{right:112px;top:23px;text-align:right;font-family:'Montserrat',sans-serif;white-space:nowrap}
.helpline .need{font-size:9px;color:var(--blue);line-height:1.3}
.helpline .phone{font-size:14px;color:var(--blue);font-weight:500;line-height:1.2}
.helpline .hours{font-size:7px;color:#444;font-weight:500;line-height:1.5}
.handset{left:676px;top:26px;width:19px;height:33px;border:1.5px solid #555;border-radius:3px}
.handset::after{content:"";position:absolute;left:2px;right:2px;top:4px;bottom:6px;border:1px solid #888}

/* nav */
.nav{left:0;top:85px;width:782px;height:26px;background:var(--nav)}
.nav ul{list-style:none;display:flex;gap:27px;position:absolute;left:107px;top:7px}
.nav li{font-family:'Montserrat',sans-serif;font-size:8.5px;color:var(--white);font-weight:500}

/* hero */
.hero-photo{left:0;top:111px;width:782px;height:288px;
  background:linear-gradient(90deg,#d8cfc6 0%,#b5a08a 22%,#e9e4df 45%,#c9cccf 60%,#efefef 100%)}
.hero-copy{left:300px;top:170px;width:153px;text-align:right;font-family:'Montserrat',sans-serif}
.hero-copy .kicker{font-size:9.5px;color:#222;font-weight:500}
.hero-copy .claim{font-size:13.5px;color:var(--red);line-height:1.35;margin-top:3px}
.arrow{top:246px;width:12px;height:12px;border-left:1.5px solid #bbb;border-bottom:1.5px solid #bbb}
.arrow.prev{left:18px;transform:rotate(45deg)}
.arrow.next{left:752px;transform:rotate(-135deg)}

/* donate panel */
.donate{left:461px;top:85px;width:234px;height:314px;background:var(--blue);color:var(--white)}
.donate h2{position:absolute;left:8px;top:22px;font-family:'Montserrat',sans-serif;font-size:20.5px;font-weight:500;letter-spacing:.2px;white-space:nowrap}
.donate .sub{position:absolute;left:10px;top:48px;font-size:8.5px;line-height:1.45}
.field{position:absolute;width:104px;height:26px;background:var(--white);color:#666;font-size:7.5px;padding:9px 10px}
.field.select::after{content:"";position:absolute;right:10px;top:10px;width:4px;height:4px;border-right:1px solid #666;border-bottom:1px solid #666;transform:rotate(45deg)}
.donate-btn{position:absolute;left:65px;top:217px;width:104px;height:26px;background:#3b3b3b;color:var(--white);font-family:'Montserrat',sans-serif;font-size:9.5px;text-align:center;line-height:26px;border-radius:2px}
.seal-round{position:absolute;left:51px;top:262px;width:30px;height:30px;border-radius:50%;background:#d9e6f2;border:2px solid #fff}
.seal-shield{position:absolute;left:101px;top:262px;width:78px;height:30px;background:#e8eef5;border-radius:3px}
.ribbon{left:649px;top:72px;width:46px;height:74px}

/* sections */
.section-title{width:782px;text-align:center;font-family:'Montserrat',sans-serif;font-size:20px;font-weight:500;letter-spacing:.3px}
.red{color:var(--red)} .blue{color:var(--blue)}

.step{top:505px;width:196px;height:105px;border:1px solid var(--line);text-align:center;background:var(--white)}
.step .badge{position:absolute;left:77px;top:-21px;width:42px;height:42px;border-radius:50%;border:1px solid var(--line);background:var(--white);display:flex;align-items:center;justify-content:center}
.step h3{margin-top:36px;font-family:'Montserrat',sans-serif;font-size:15px;font-weight:500;color:var(--red)}
.step p{margin:6px auto 0;width:152px;font-size:5.6px;line-height:1.6;color:var(--muted)}

.band{left:0;top:658px;width:782px;height:285px;background:var(--gray-band)}
.reason{width:140px;text-align:center}
.reason svg{display:block;margin:0 auto 5px}
.reason h4{font-family:'Montserrat',sans-serif;font-size:9.3px;font-weight:500;color:var(--blue);white-space:nowrap}
.reason p{font-size:5.8px;line-height:1.6;color:#444;margin-top:3px}

.checks{left:86px;top:1008px;list-style:none}
.checks li{font-family:'Montserrat',sans-serif;font-size:9.5px;color:#333;height:21px;display:flex;gap:9px;align-items:flex-start}
.checks svg{margin-top:2px}
.sub-title{font-family:'Montserrat',sans-serif;font-size:15.5px;font-weight:500;top:982px}
.prog{width:133px;height:43px;border:1px solid var(--line);display:flex;align-items:center;gap:10px;padding-left:12px;font-size:6.5px;line-height:1.55;color:#555;background:var(--white)}

.footer{left:0;top:1146px;width:782px;height:54px;background:var(--footer)}
.footer .links{position:absolute;left:86px;top:13px;font-size:6.5px;color:#555;word-spacing:2px}
.footer .copy{position:absolute;left:86px;top:31px;font-size:6.5px;color:#555}
.social{top:1165px;width:16px;height:16px;border-radius:50%}
</style>
</head>
<body>

<header>
  <div class="abs brand"><span class="brand-mark"></span><span class="brand-name">Wheels for Servicemen</span></div>
  <div class="abs helpline">
    <div class="need">We need your help</div>
    <div class="phone">Call 1-800-555-0142</div>
    <div class="hours">Live Operators Available 7 Days A Week</div>
  </div>
  <div class="abs handset"></div>
</header>

<div class="abs hero-photo" role="img" aria-label="Smiling soldier in camouflage carrying a young girl on his shoulders beside a silver sedan, in a bright living room"></div>

<nav class="abs nav">
  <ul><li>How it works</li><li>Charities</li><li>Tax Deduction</li><li>FAQs</li><li>Contact Us</li></ul>
</nav>

<div class="abs hero-copy">
  <div class="kicker">DONATE YOUR CAR :</div>
  <div class="claim">Full Tax Deduction<br>Running or Not</div>
</div>
<span class="abs arrow prev"></span>
<span class="abs arrow next"></span>

<form class="abs donate">
  <h2>DONATE HERE</h2>
  <p class="sub">Please fill out form or<br>Call toll-free 1-800-555-0142</p>
  <div class="field" style="left:9px;top:88px">Name</div>
  <div class="field" style="left:120px;top:88px">Email</div>
  <div class="field" style="left:9px;top:120px">Phone</div>
  <div class="field" style="left:120px;top:120px">Mobile</div>
  <div class="field" style="left:9px;top:152px">Address</div>
  <div class="field" style="left:120px;top:152px">City</div>
  <div class="field select" style="left:9px;top:184px">State</div>
  <div class="field" style="left:120px;top:184px">Zip Code</div>
  <div class="donate-btn">DONATE NOW</div>
  <span class="seal-round"></span>
  <span class="seal-shield"></span>
</form>
<svg class="abs ribbon" viewBox="0 0 46 74" aria-hidden="true">
  <path d="M0 0H46V74L23 62L0 74Z" fill="#e9edf2"/>
  <rect x="4" y="4" width="38" height="24" fill="#1f3f86"/>
</svg>

<h2 class="abs section-title red" style="top:442px">HOW IT WORKS</h2>

<div class="abs step" style="left:86px">
  <span class="badge"><svg width="16" height="16" viewBox="0 0 24 24"><path d="M6.6 10.8a15 15 0 0 0 6.6 6.6l2.2-2.2a1 1 0 0 1 1-.25 11.4 11.4 0 0 0 3.6.57 1 1 0 0 1 1 1V20a1 1 0 0 1-1 1A17 17 0 0 1 3 4a1 1 0 0 1 1-1h3.5a1 1 0 0 1 1 1c0 1.25.2 2.45.57 3.57a1 1 0 0 1-.25 1z" fill="#a81c1c"/></svg></span>
  <h3>Call Us</h3>
  <p>Nullam sed metus cursus urna varius vulputate. Praesent mollis auctor velit at pellentesque. Pellentesque habitant morbi.</p>
</div>
<div class="abs step" style="left:293px">
  <span class="badge"><svg width="18" height="18" viewBox="0 0 24 24" fill="none" stroke="#a81c1c" stroke-width="2.2"><rect x="2" y="6" width="10" height="6" rx="3" transform="rotate(45 7 9)"/><rect x="12" y="12" width="10" height="6" rx="3" transform="rotate(45 17 15)"/></svg></span>
  <h3>We Tow It</h3>
  <p>Nullam sed metus cursus urna varius vulputate. Praesent mollis auctor velit at pellentesque. Pellentesque habitant morbi.</p>
</div>
<div class="abs step" style="left:499px">
  <span class="badge"><svg width="18" height="18" viewBox="0 0 24 24" fill="none" stroke="#a81c1c" stroke-width="2"><path d="M18 13v6a2 2 0 0 1-2 2H5a2 2 0 0 1-2-2V8a2 2 0 0 1 2-2h6"/><path d="M18 3l3 3-9 9H9v-3z"/></svg></span>
  <h3>Tax Write-Off</h3>
  <p>Nullam sed metus cursus urna varius vulputate. Praesent mollis auctor velit at pellentesque. Pellentesque habitant morbi.</p>
</div>

<section class="abs band"></section>
<h2 class="abs section-title blue" style="top:692px">WHY DONATE YOUR CAR TO US?</h2>

<div class="abs reason" style="left:72px;top:740px">
  <svg width="20" height="20" viewBox="0 0 24 24"><path d="M12 1l2.4 2.6 3.4-.9.9 3.4 3.4.9-.9 3.4L23.8 12l-2.6 2.4.9 3.4-3.4.9-.9 3.4-3.4-.9L12 23.8l-2.4-2.6-3.4.9-.9-3.4-3.4-.9.9-3.4L.2 12l2.6-2.4-.9-3.4 3.4-.9.9-3.4 3.4.9z" fill="#0b6dd1"/></svg>
  <h4>IRS 501(c)3 Approved</h4>
  <p>Free 24/7 Pickup with No DMV Hassles.</p>
</div>
<div class="abs reason" style="left:231px;top:740px">
  <svg width="20" height="20" viewBox="0 0 24 24" fill="none" stroke="#0b6dd1" stroke-width="2.2"><rect x="2" y="6" width="10" height="6" rx="3" transform="rotate(45 7 9)"/><rect x="12" y="12" width="10" height="6" rx="3" transform="rotate(45 17 15)"/></svg>
  <h4>Free Local Towing to You</h4>
  <p>We will pick up your car donation, running or not, when it's most convenient, at home or work.</p>
</div>
<div class="abs reason" style="left:400px;top:740px">
  <svg width="22" height="20" viewBox="0 0 24 22"><path d="M4 9l2-5h12l2 5h1a1 1 0 0 1 1 1v6h-2v3h-3v-3H7v3H4v-3H2v-6a1 1 0 0 1 1-1z" fill="#0b6dd1"/><circle cx="6.5" cy="12.5" r="1.5" fill="#f4f4f4"/><circle cx="17.5" cy="12.5" r="1.5" fill="#f4f4f4"/><path d="M7 8.5l1.3-3h7.4l1.3 3z" fill="#f4f4f4"/></svg>
  <h4>All Cars Accepted</h4>
  <p>We take your car regardless of its condition or registration status.</p>
</div>
<div class="abs reason" style="left:560px;top:740px">
  <svg width="20" height="20" viewBox="0 0 24 24" fill="none" stroke="#0b6dd1" stroke-width="1.8"><rect x="4" y="2" width="16" height="20"/><path d="M7 5h10v4H7zM7 12h2M11 12h2M15 12h2M7 15h2M11 15h2M15 15h2M7 18h2M11 18h2M15 18h2"/></svg>
  <h4>Income Tax Deduction</h4>
  <p>We issue you an IRS tax receipt &amp; offer the largest resale network to get you the highest tax write-off possible.</p>
</div>

<div class="abs reason" style="left:127px;top:834px">
  <svg width="20" height="20" viewBox="0 0 24 24" fill="none" stroke="#0b6dd1" stroke-width="1.8"><path d="M5 2h10l4 4v16H5z"/><path d="M8 11h8M8 14h8M8 17h8"/></svg>
  <h4>No Paperwork Hassles</h4>
  <p>We take any car and handle everything: DMV, Smog and IRS paperwork.</p>
</div>
<div class="abs reason" style="left:305px;top:834px;width:172px">
  <svg width="26" height="20" viewBox="0 0 30 20" fill="none" stroke="#0b6dd1" stroke-width="2"><rect x="2" y="3" width="26" height="14"/><circle cx="15" cy="10" r="4"/></svg>
  <h4>Car donations help fund programs</h4>
  <p>And benefit National Servicemen Support Fund. An IRS 501(c)3 nonprofit organization.</p>
</div>
<div class="abs reason" style="left:515px;top:834px">
  <svg width="20" height="20" viewBox="0 0 24 24" fill="none" stroke="#0b6dd1" stroke-width="1.8"><rect x="3" y="4" width="18" height="18"/><path d="M7 2v4M17 2v4M3 9h18M7 13h2M11 13h2M15 13h2M7 17h2M11 17h2M15 17h2"/></svg>
  <h4>Schedule a Free Pickup</h4>
  <p>Complete the form and a representative will call you to arrange a convenient time to pickup your car.</p>
</div>

<h2 class="abs sub-title red" style="left:86px">DONATE YOUR CAR TODAY!</h2>
<ul class="abs checks">
  <li><svg width="9" height="8" viewBox="0 0 10 8"><path d="M1 4l3 3 5-6" fill="none" stroke="#555" stroke-width="2"/></svg>You have no costs.</li>
  <li><svg width="9" height="8" viewBox="0 0 10 8"><path d="M1 4l3 3 5-6" fill="none" stroke="#555" stroke-width="2"/></svg>Free towing, running or not.</li>
  <li><svg width="9" height="8" viewBox="0 0 10 8"><path d="M1 4l3 3 5-6" fill="none" stroke="#555" stroke-width="2"/></svg>We issue you an IRS tax receipt.</li>
  <li><svg width="9" height="8" viewBox="0 0 10 8"><path d="M1 4l3 3 5-6" fill="none" stroke="#555" stroke-width="2"/></svg>We take care of all paperwork.</li>
  <li><svg width="9" height="8" viewBox="0 0 10 8"><path d="M1 4l3 3 5-6" fill="none" stroke="#555" stroke-width="2"/></svg>And we take care of DMV &amp; Smog issues.</li>
</ul>

<h2 class="abs sub-title blue" style="left:423px">CAR DONATION PROGRAM</h2>
<div class="abs prog" style="left:424px;top:1010px">
  <span style="width:34px;height:22px;background:#777;border-radius:4px 8px 10px 6px;display:inline-block" role="img" aria-label="Map of the United States"></span>
  <span>Donations<br>accepted nationwide</span>
</div>
<div class="abs prog" style="left:563px;top:1010px">
  <svg width="38" height="22" viewBox="0 0 38 22" fill="none" stroke="#666" stroke-width="1.6"><path d="M2 16V10l3-1 4-6h14l5 6 7 2v5z"/><circle cx="10" cy="17" r="3" fill="#fff"/><circle cx="28" cy="17" r="3" fill="#fff"/></svg>
  <span>All vehicle<br>types welcome</span>
</div>
<div class="abs prog" style="left:424px;top:1061px">
  <svg width="34" height="28" viewBox="0 0 34 28" fill="none" stroke="#666" stroke-width="1.6"><path d="M9 2h12l5 5v19H9z"/><path d="M13 11h9M13 15h9M13 19h6"/></svg>
  <span>Tax deductible</span>
</div>
<div class="abs prog" style="left:563px;top:1061px">
  <svg width="34" height="28" viewBox="0 0 34 28" fill="none" stroke="#666" stroke-width="1.6"><path d="M3 2l9 16M3 22V4M3 22h28v-6l-6-4h-6v10"/><circle cx="10" cy="23" r="3" fill="#fff"/><circle cx="26" cy="23" r="3" fill="#fff"/></svg>
  <span>Towing is free</span>
</div>

<footer class="abs footer">
  <div class="links">Home &nbsp;| &nbsp;How it works &nbsp;| &nbsp;Charities &nbsp;| &nbsp;Tax Deduction &nbsp;| &nbsp;FAQs &nbsp;| &nbsp;Contact Us</div>
  <div class="copy">Copyright &copy; 2016 &nbsp;Company name. &nbsp;All rights reserved.</div>
</footer>
<span class="abs social" style="left:657px;background:#3b5a9a"></span>
<span class="abs social" style="left:678px;background:#2aa3ef"></span>

</body>
</html>
```